Lush Satchel

I am developing a web site which sells preowned high end designer handbags and accessories. Some of the brands include: Varenne, Marcel Ostrand & Belmo, to name a few. I am after a luxurious and high end feel.

Some brands I like that express this feel include: Quintel, Belmo, fabcloset.com, pursepassonpaw.com

I am after a logo, business card, letterhead, with compliments, address label and envelope designs.
The business name is Lush satchel, and the website will be www.lushsatchel.com.au. I have thoughts of using LSC as a logo or LUSH satchel.com.au

I don't want a large logo, it needs to blend in with the name in some way - or may not need an image at all, if the style of the font speaks to the brand.

Thank-you
Updates

Project Deadline Extended
Reason: I would like to give designers plenty of time to be able to submit a design.

Target Market(s)

Women, aged 25-60 who are into fashion

Industry/Entity Type

Business

Requirements
Must have
• High End
Luxurious

```html
<!DOCTYPE html>
<html lang="en">
<head>
<meta charset="utf-8">
<title>Lush Satchel – Business Card</title>
<link rel="stylesheet" href="https://fonts.googleapis.com/css2?family=Arimo:wght@400;700&display=swap">
<style>
  :root {
    --backdrop: #f2f0ea;
    --card-edge: #1a1a1a;
    --card-base: #e7e7e7;
    --frame: #e8dfb5;
    --panel-white: #ffffff;
    --panel-shade: #ececec;
    --ink: #e3d8a6;
    --mark-square: #e2e2e2;
  }
  * { box-sizing: border-box; margin: 0; padding: 0; }
  html, body {
    width: 1200px; height: 1200px; overflow: hidden;
    background: var(--backdrop);
  }
  .canvas { position: relative; width: 1200px; height: 1200px; }

  .business-card {
    position: absolute; left: 96px; top: 310px;
    width: 1008px; height: 574px;
    background: var(--card-base);
    border: 2px solid var(--card-edge);
  }
  .card-frame {
    position: absolute; left: 28px; top: 28px;
    width: 950px; height: 516px;
    background: var(--frame);
  }
  .card-panel {
    position: absolute; left: 20px; top: 30px;
    width: 898px; height: 452px;
    background: radial-gradient(ellipse at 50% 45%, var(--panel-white) 55%, var(--panel-shade) 100%);
    font-family: "Arimo", Arial, sans-serif;
    font-weight: 700;
    color: var(--ink);
    text-align: center;
  }
  .holder-name {
    position: absolute; left: 0; right: 0; top: 46px;
    font-size: 30px; line-height: 1; text-decoration: underline;
    text-underline-offset: 3px;
  }
  .holder-role {
    position: absolute; left: 0; right: 0; top: 84px;
    font-size: 30px; line-height: 1;
  }
  .brand-lockup {
    position: absolute; left: 150px; top: 164px;
    width: 604px; height: 126px;
    display: flex; align-items: center; justify-content: center; gap: 26px;
  }
  .brand-square {
    width: 64px; height: 64px; background: var(--mark-square);
  }
  .brand-name {
    font-size: 58px; line-height: 1; color: var(--ink); font-weight: 700;
  }
  .contact-list {
    position: absolute; left: 0; right: 0; top: 302px;
    list-style: none; font-size: 24px; line-height: 29px;
  }
</style>
</head>
<body>
<main class="canvas">
  <section class="business-card" aria-label="Lush Satchel business card">
    <div class="card-frame">
      <div class="card-panel">
        <p class="holder-name">Mara</p>
        <p class="holder-role">Director</p>
        <div class="brand-lockup">
          <span class="brand-square"></span>
          <span class="brand-name">Lush Satchel</span>
        </div>
        <ul class="contact-list">
          <li>Address: 212 Harlow Lane, Brightvale, VIC 3999</li>
          <li>Phone: 410-555-019</li>
          <li>Fax: 410-555-019</li>
          <li>Email: mara@lushsatchel.com.au</li>
          <li>Web: www.lushsatchel.com.au</li>
        </ul>
      </div>
    </div>
  </section>
</main>
</body>
</html>
```